I need a business card design for a new business based in South West Australia.
I specialize in residential window cleaning & general handyman maintenance.

Dale Marsh - 412 SILVER HAWK DETAILING
- Window Cleaning
- House Maintenance

```html
<!DOCTYPE html>
<html lang="en">
<head>
<meta charset="utf-8">
<title>412 Silver Hawk Detailing – Business Card</title>
<link rel="stylesheet" href="https://fonts.googleapis.com/css2?family=Old+Standard+TT:wght@400;700&display=swap">
<style>
  :root {
    --page-bg: #d9d6d1;
    --card-navy-deep: #0d1522;
    --card-navy: #1c2d45;
    --card-navy-soft: #2a3f5c;
    --metal-light: #f4f1ea;
    --metal-gold: #c8a27a;
    --metal-silver: #cfd3d8;
    --copper-light: #f2b7b0;
    --copper: #b8685c;
    --subtitle: #eef0f2;
    --photo-blue: #1f3a5c;
    --photo-deep: #0e1a2b;
    --photo-accent: #4a7db3;
  }
  * { margin: 0; padding: 0; box-sizing: border-box; }
  html, body {
    width: 1200px;
    height: 970px;
    overflow: hidden;
    background: var(--page-bg);
  }
  .canvas {
    position: relative;
    width: 1200px;
    height: 970px;
  }
  .business-card {
    position: absolute;
    left: 50px;
    top: 156px;
    width: 1100px;
    height: 658px;
    overflow: hidden;
    background: radial-gradient(ellipse at 48% 30%, var(--card-navy-soft) 0%, var(--card-navy) 40%, var(--card-navy-deep) 100%);
    box-shadow: 0 14px 40px rgba(0,0,0,0.25);
    font-family: "Old Standard TT", Georgia, serif;
  }
  .card-art {
    position: absolute;
    inset: 0;
  }
  .text-column {
    position: absolute;
    left: 0;
    top: 0;
    width: 1096px;
    height: 100%;
    text-align: center;
  }
  .metal-text {
    background: linear-gradient(90deg, var(--metal-gold) 0%, var(--metal-light) 30%, var(--metal-silver) 55%, var(--metal-gold) 85%, var(--metal-light) 100%);
    -webkit-background-clip: text;
    background-clip: text;
    color: transparent;
  }
  .company-name {
    position: absolute;
    left: 0; right: 0;
    top: 88px;
    font-size: 52px;
    font-weight: 700;
    letter-spacing: 1px;
    line-height: 1;
  }
  .tagline {
    position: absolute;
    left: 0; right: 0;
    top: 162px;
    font-size: 33px;
    font-weight: 700;
    line-height: 51px;
    color: var(--subtitle);
  }
  .divider {
    position: absolute;
    left: 142px;
    width: 814px;
    top: 306px;
    height: 4px;
    background: linear-gradient(90deg, var(--metal-gold), var(--metal-light) 40%, var(--metal-silver) 70%, var(--metal-light));
  }
  .person-name {
    position: absolute;
    left: 0; right: 0;
    top: 362px;
    font-size: 70px;
    font-weight: 700;
    line-height: 1;
  }
  .services {
    position: absolute;
    left: 0; right: 0;
    top: 492px;
    list-style: none;
    font-size: 37px;
    font-weight: 700;
    line-height: 54px;
  }
  .services li {
    background: linear-gradient(90deg, var(--copper-light), var(--copper) 60%, var(--copper-light));
    -webkit-background-clip: text;
    background-clip: text;
    color: transparent;
    display: table;
    margin: 0 auto;
  }
</style>
</head>
<body>
<div class="canvas">
  <div class="business-card">
    <svg class="card-art" width="1100" height="658" viewBox="0 0 1100 658">
      <defs>
        <linearGradient id="photoFill" x1="0" y1="0" x2="1" y2="1">
          <stop offset="0" stop-color="var(--photo-deep)"/>
          <stop offset="0.55" stop-color="var(--photo-blue)"/>
          <stop offset="1" stop-color="var(--photo-accent)"/>
        </linearGradient>
        <linearGradient id="houseFill" x1="0" y1="0" x2="0" y2="1">
          <stop offset="0" stop-color="#3a3f55" stop-opacity="0"/>
          <stop offset="1" stop-color="#5a4a58" stop-opacity="0.45"/>
        </linearGradient>
      </defs>
      <rect class="house-backdrop" role="img" aria-label="Faint illustration of a house roofline" x="40" y="400" width="640" height="258" fill="url(#houseFill)"/>
      <polygon class="squeegee-photo" role="img" aria-label="Photo of a squeegee wiping a wet window pane" points="1043,0 1100,0 1100,658 740,658" fill="url(#photoFill)"/>
      <line class="squeegee-edge" x1="1043" y1="0" x2="740" y2="658" stroke="var(--metal-silver)" stroke-width="5" stroke-opacity="0.8"/>
    </svg>

    <div class="text-column">
      <h1 class="company-name metal-text">412 SILVER HAWK DETAILING</h1>
      <p class="tagline">residential window cleaning &amp;<br>general handyman maintenance</p>
      <div class="divider"></div>
      <h2 class="person-name metal-text">Dale Marsh</h2>
      <ul class="services">
        <li>House Maintenance</li>
        <li>Window Cleaning</li>
      </ul>
    </div>
  </div>
</div>
</body>
</html>
```